R. Talmont Realty, Inc business card (2 sided), letterhead (1 sided) & #10 envelope (1 sided)

business card of standard size utilizing the attached logo. Side one with logo, Owen Talmont (my name), President / Broker (title), 805-317-2684 (phone), www.rtalmontrealty.example (website), 1726 Harlow Avenue, Suite 4052 San Luis Obiso, CA 93628 (business address) owen.rtalmontrealty@mailbox.example (e-mail address),
Side two - Log

Letterhead and #10 envelope in the same theme
Updates

Project Deadline Extended
Reason: I think a 2 day deadline may be a bit ambitious on my part. I have extended the deadline to 4 days. Thanks!

Industry/Entity Type

Business

```html
<!DOCTYPE html>
<html lang="en">
<head>
<meta charset="utf-8">
<title>R. Talmont Realty, Inc – Business Card</title>
<link rel="stylesheet" href="https://fonts.googleapis.com/css2?family=Merriweather:wght@400;700&family=Open+Sans:wght@400;600&display=swap">
<style>
  :root {
    --stage: #e9e6e1;
    --card-white: #ffffff;
    --brand-blue: #1b6f96;
    --brand-blue-deep: #0c4f6e;
    --brand-blue-light: #2b8ab5;
    --charcoal: #3b3b3d;
    --ink: #2a2a2a;
    --rule: #c9c9c9;
  }
  * { margin: 0; padding: 0; box-sizing: border-box; }
  html, body {
    width: 1200px; height: 1183px; overflow: hidden;
    background: var(--stage);
  }
  .canvas { position: relative; width: 1200px; height: 1183px; }

  .card {
    position: absolute;
    width: 913px; height: 519px;
    overflow: hidden;
    box-shadow: 0 6px 18px rgba(0,0,0,0.18);
  }
  .card--front { left: 24px; top: 46px; background: var(--card-white); }
  .card--back {
    left: 250px; top: 615px;
    background: radial-gradient(ellipse at 50% 35%, var(--brand-blue-light) 0%, var(--brand-blue) 45%, var(--brand-blue-deep) 100%);
  }

  .wordmark {
    position: absolute;
    font-family: 'Merriweather', serif;
    font-weight: 400;
    font-size: 46px;
    white-space: nowrap;
    transform: translate(-50%, -50%);
    display: flex; align-items: center; gap: 18px;
  }
  .wordmark__mark { width: 22px; height: 22px; display: inline-block; }
  .card--front .wordmark { left: 448px; top: 157px; color: var(--brand-blue); }
  .card--front .wordmark__mark { background: var(--brand-blue); }
  .card--back .wordmark { left: 456px; top: 220px; color: #ffffff; }
  .card--back .wordmark__mark { background: #ffffff; }

  .person {
    position: absolute; right: 526px; top: 327px;
    text-align: right;
    font-family: 'Merriweather', serif; font-weight: 700;
  }
  .person__name { color: var(--brand-blue); font-size: 31px; line-height: 1.3; }
  .person__title { color: var(--ink); font-size: 25px; line-height: 1.45; }

  .divider {
    position: absolute; left: 408px; top: 300px;
    width: 1px; height: 111px; background: var(--rule);
  }

  .contacts {
    position: absolute; left: 420px; top: 297px;
    list-style: none;
    font-family: 'Open Sans', sans-serif; font-size: 21px; color: var(--ink);
  }
  .contacts li { display: flex; align-items: center; gap: 6px; height: 41px; }
  .contacts svg { width: 18px; height: 18px; flex: none; fill: var(--charcoal); }

  .footer-band {
    position: absolute; left: 0; bottom: 0;
    width: 913px; height: 78px;
    background: linear-gradient(180deg, var(--charcoal) 0 10px, var(--card-white) 10px 16px, transparent 16px),
                linear-gradient(90deg, var(--brand-blue-deep) 0%, var(--brand-blue-light) 50%, var(--brand-blue-deep) 100%);
  }

  .back-url {
    position: absolute; left: 0; right: 0; top: 428px;
    text-align: center;
    font-family: 'Open Sans', sans-serif; font-weight: 600;
    font-size: 27px; letter-spacing: 4px; color: #ffffff;
  }
</style>
</head>
<body>
<main class="canvas">

  <section class="card card--front" aria-label="Business card front">
    <div class="wordmark"><span class="wordmark__mark"></span>R. Talmont Realty, Inc</div>

    <div class="person">
      <p class="person__name">Owen Talmont</p>
      <p class="person__title">President / Broker</p>
    </div>

    <div class="divider"></div>

    <ul class="contacts">
      <li>
        <svg viewBox="0 0 24 24" aria-hidden="true"><path d="M6.6 10.8a15.1 15.1 0 0 0 6.6 6.6l2.2-2.2c.3-.3.7-.4 1-.2 1.1.4 2.3.6 3.6.6.6 0 1 .4 1 1V20c0 .6-.4 1-1 1C10.6 21 3 13.4 3 4c0-.6.4-1 1-1h3.5c.6 0 1 .4 1 1 0 1.3.2 2.5.6 3.6.1.3 0 .7-.2 1z"/></svg>
        805-317-2684
      </li>
      <li>
        <svg viewBox="0 0 24 24" aria-hidden="true"><path d="M3 6h18v12H3z M3 6l9 7 9-7" fill="none" stroke="#3b3b3d" stroke-width="2.4"/></svg>
        owen.rtalmontrealty@mailbox.example
      </li>
      <li>
        <svg viewBox="0 0 24 24" aria-hidden="true"><circle cx="12" cy="12" r="9" fill="none" stroke="#3b3b3d" stroke-width="2"/><path d="M3 12h18M12 3c3 3 3 15 0 18M12 3c-3 3-3 15 0 18" fill="none" stroke="#3b3b3d" stroke-width="1.6"/></svg>
        www.rtalmontrealty.example
      </li>
    </ul>

    <div class="footer-band" role="img" aria-label="Decorative charcoal and blue wave band along the bottom edge"></div>
  </section>

  <section class="card card--back" aria-label="Business card back">
    <div class="wordmark"><span class="wordmark__mark"></span>R. Talmont Realty, Inc</div>
    <p class="back-url">www.rtalmontrealty.example</p>
  </section>

</main>
</body>
</html>
```